A Modern & Sleek "Coming Soon" Page for an A.I Recruiting App

For the “Coming Soon” website, a simple background with no people in it. I've attached an A.I image of what the page should generally look like.

- A single mobile phone as the main focus where the user actually clicks on the, “notify me” button (after entering their email address).
- In the background where the pillars/columns are seen in the example, should be subtle pad locks that are in their opened position with a key inside the lock. I've attached images to try to illustrate this idea, but they are far away in style from what I'm looking for.

SLOGAN: Unlocking the power of meaningful connections
LOGO/TITLE: Should be the name as shown in image with only the name "KelvoLink" on it
COLORS: Purplish/blue hues. Should not be too feminine
NOTE: The user should only click once when signing up/entering their email.

Product: A recruiting platform that matches employers/employees with A.I. and prioritizing cultural fit/values system before skills. The industry we are tackling first is the caregiving industry (nannies, tutors, elderly). All users will be background screened and that info lives on the blockchain. All users will have the option to review and be reviewed/rated.

```html
<!DOCTYPE html>
<html lang="en">
<head>
<meta charset="UTF-8">
<title>KelvoLink – Coming Soon</title>
<link href="https://fonts.googleapis.com/css2?family=Montserrat:wght@300;500;600;800&display=swap" rel="stylesheet">
<style>
  :root {
    --bg-deep: #1a0b2e;
    --bg-mid: #2a1347;
    --bg-glow: #3b1d5e;
    --brand-magenta: #b3308f;
    --button-fill: #b5258a;
    --text-light: #ffffff;
    --text-soft: #d9c8ee;
    --art-dark: #241038;
    --art-light: #5c3585;
    --device-frame: #140822;
    --device-edge: #4a2472;
    --screen-top: #6a2f95;
    --screen-bottom: #1e0c33;
  }
  * { margin: 0; padding: 0; box-sizing: border-box; }
  html, body {
    width: 1200px;
    height: 857px;
    overflow: hidden;
    background: var(--bg-deep);
  }
  .page {
    position: relative;
    width: 1200px;
    height: 857px;
    overflow: hidden;
    font-family: 'Montserrat', sans-serif;
    color: var(--text-light);
    background:
      radial-gradient(ellipse 70% 45% at 55% 20%, var(--bg-glow) 0%, transparent 70%),
      radial-gradient(ellipse 80% 40% at 60% 85%, var(--bg-mid) 0%, transparent 70%),
      var(--bg-deep);
  }

  /* Padlock artwork area */
  .lock-art {
    position: absolute;
    left: 26px;
    top: 266px;
    width: 300px;
    height: 390px;
    border-radius: 30px;
    background: radial-gradient(ellipse at 55% 65%, var(--art-light) 0%, var(--art-dark) 60%, transparent 100%);
  }

  /* Phone */
  .phone {
    position: absolute;
    left: 288px;
    top: 140px;
    width: 300px;
    height: 548px;
    border-radius: 44px;
    border: 9px solid var(--device-frame);
    box-shadow: 0 0 0 2px var(--device-edge), 0 30px 60px rgba(0,0,0,0.5);
    background: linear-gradient(170deg, var(--screen-top) 0%, #40186a 45%, var(--screen-bottom) 100%);
    transform: rotate(2deg);
    overflow: hidden;
  }
  .phone-notch {
    position: absolute;
    left: 50%;
    top: 0;
    width: 120px;
    height: 24px;
    transform: translateX(-50%);
    border-radius: 0 0 16px 16px;
    background: var(--device-frame);
  }
  .screen-brand {
    position: absolute;
    top: 110px;
    left: 0;
    width: 100%;
    text-align: center;
    font-weight: 300;
    font-size: 24px;
    letter-spacing: 1px;
    text-transform: uppercase;
    color: var(--brand-magenta);
  }
  .screen-slogan {
    position: absolute;
    top: 272px;
    left: 40px;
    width: 200px;
    text-align: center;
    font-weight: 500;
    font-size: 13px;
    line-height: 18px;
    color: var(--text-soft);
  }
  .notify-button {
    position: absolute;
    top: 420px;
    left: 46px;
    width: 190px;
    height: 40px;
    border: 2px solid var(--text-soft);
    border-radius: 20px;
    background: transparent;
    color: var(--text-light);
    font-family: 'Montserrat', sans-serif;
    font-weight: 800;
    font-size: 18px;
    cursor: pointer;
  }
  .screen-note {
    position: absolute;
    top: 472px;
    left: 40px;
    width: 200px;
    text-align: center;
    font-weight: 500;
    font-size: 11px;
    line-height: 15px;
    color: var(--text-soft);
  }

  /* Headline block */
  .brand-name {
    position: absolute;
    left: 643px;
    top: 274px;
    font-weight: 300;
    font-size: 74px;
    line-height: 1;
    letter-spacing: 2px;
    text-transform: uppercase;
    color: var(--brand-magenta);
  }
  .slogan {
    position: absolute;
    left: 654px;
    top: 372px;
    width: 500px;
    font-weight: 600;
    font-size: 26px;
    line-height: 34px;
  }
  .signup-button {
    position: absolute;
    left: 653px;
    top: 465px;
    width: 175px;
    height: 58px;
    border: none;
    border-radius: 29px;
    background: var(--button-fill);
    color: var(--text-light);
    font-family: 'Montserrat', sans-serif;
    font-weight: 500;
    font-size: 20px;
    cursor: pointer;
  }
</style>
</head>
<body>
  <main class="page">
    <div class="lock-art" role="img" aria-label="Open padlock with a glowing key inserted in its keyhole"></div>

    <div class="phone">
      <div class="phone-notch"></div>
      <p class="screen-brand">KelvoLink</p>
      <p class="screen-slogan">Unlocking the power of meaningful connections</p>
      <button class="notify-button" type="button">Notify Me</button>
      <p class="screen-note">Enter your email for<br>early access</p>
    </div>

    <h1 class="brand-name">KelvoLink</h1>
    <p class="slogan">Unlocking the power of meaningful connections</p>
    <button class="signup-button" type="button">Sign Up</button>
  </main>
</body>
</html>
```